Small Catering Menu

I am looking to make a small menu for catering for my company. I am thinking of a small A5 size booklet which will also have some pictures and the cover needs to be attractive.
Likely to be 8-12 pages depending upon your design (could be less or more). I need 2-3 pages as proposal concept (Cover, inside first page and one menu page) and if we like it we will make the project guaranteed before finishing the rest of the project to add security for the designer.
Pictures will be provided to the designer whose concept is the best as they are too heavy. But use generic photos for now (rather large ones) if possible.
Logo is available and so is the inside text as well as some other tidbits.
I will provide the fonts too to ensure it maintains the corporate integrity that we are following.
Industry/Entity Type
Catering

```html
<!DOCTYPE html>
<html lang="en">
<head>
<meta charset="utf-8">
<title>Harbor Table Catering – Menu Spread</title>
<link rel="stylesheet" href="https://fonts.googleapis.com/css2?family=PT+Sans:wght@400;700&display=swap">
<style>
  :root {
    --charcoal: #1e1e1e;
    --cocoa: #6a4939;
    --cocoa-deep: #5c3f31;
    --brick: #d24a30;
    --coral: #e24e3f;
    --white: #ffffff;
    --paper: #f7f5f3;
    --wheat: #e2b24f;
  }
  * { margin: 0; padding: 0; box-sizing: border-box; }
  html, body { width: 1200px; height: 858px; overflow: hidden; }
  body {
    position: relative;
    background: var(--charcoal);
    font-family: "PT Sans", Arial, sans-serif;
    color: var(--white);
  }

  /* Back cover */
  .back-cover {
    position: absolute; left: 0; top: 127px; width: 596px; height: 546px;
    background: linear-gradient(90deg, var(--cocoa) 0%, var(--cocoa-deep) 100%);
  }
  .brand-frame {
    position: absolute; left: 94px; top: 45px; width: 418px; height: 322px;
    border: 1px solid var(--white);
    display: flex; align-items: center; justify-content: center; gap: 16px;
  }
  .brand-name {
    font-weight: 700; color: var(--white); text-align: center;
    letter-spacing: 1px; line-height: 1.05;
  }
  .brand-frame .brand-name { font-size: 46px; }
  .brand-dot { width: 24px; height: 24px; border-radius: 50%; background: var(--wheat); flex: none; }

  .contact { position: absolute; left: 0; width: 596px; text-align: center; }
  .contact-phone { top: 398px; font-size: 20px; line-height: 24px; }
  .contact-line { font-size: 8px; line-height: 10px; }
  .contact-email { top: 425px; }
  .contact-domain { top: 435px; }
  .contact-rule {
    position: absolute; left: 163px; top: 471px; width: 276px; height: 1px;
    background: rgba(255,255,255,0.7);
  }
  .contact-web { top: 481px; font-size: 10px; line-height: 12px; letter-spacing: 4px; }

  .accent-band {
    position: absolute; left: 0; top: 673px; width: 1200px; height: 24px;
    background: var(--brick);
  }

  /* Front cover */
  .front-page {
    position: absolute; left: 596px; top: 0; width: 604px; height: 673px;
    background: var(--paper);
  }
  .front-header {
    position: absolute; left: 0; top: 0; width: 604px; height: 148px;
    background: var(--coral); text-align: center;
  }
  .front-header .brand-name {
    position: absolute; left: 0; width: 100%; top: 20px; font-size: 36px;
  }
  .front-intro {
    position: absolute; left: 0; width: 100%; top: 111px;
    font-size: 11px; font-weight: 700; line-height: 13px;
  }

  .photo { position: absolute; }
  .photo-hero {
    left: 9px; top: 157px; width: 585px; height: 370px;
    background:
      radial-gradient(ellipse 45% 40% at 82% 22%, #f1ebe2 0%, #e6d9c6 55%, rgba(230,217,198,0) 100%),
      radial-gradient(ellipse 35% 30% at 38% 12%, #d98e4f 0%, rgba(217,142,79,0) 100%),
      radial-gradient(ellipse 30% 30% at 72% 78%, #9fa045 0%, rgba(159,160,69,0) 100%),
      radial-gradient(ellipse 70% 60% at 40% 62%, #f0c65e 0%, #d9a13f 45%, #9b6627 80%, #4b2e16 100%);
  }
  .photo-cake {
    left: 9px; top: 540px; width: 188px; height: 123px;
    background:
      radial-gradient(ellipse 45% 40% at 40% 50%, #b98a5c 0%, rgba(185,138,92,0) 100%),
      linear-gradient(180deg, #5a3519 0%, #3d2412 70%, #2a180c 100%);
  }
  .photo-juice {
    left: 208px; top: 540px; width: 187px; height: 123px;
    background:
      radial-gradient(ellipse 45% 40% at 50% 60%, #e8473a 0%, rgba(232,71,58,0) 100%),
      linear-gradient(180deg, #b8672f 0%, #94491f 60%, #5c2c14 100%);
  }
  .photo-fruit {
    left: 406px; top: 540px; width: 188px; height: 123px;
    background:
      radial-gradient(ellipse 30% 35% at 72% 50%, #e77d2c 0%, rgba(231,125,44,0) 100%),
      radial-gradient(ellipse 18% 30% at 20% 45%, #8a9a3a 0%, rgba(138,154,58,0) 100%),
      linear-gradient(180deg, #6b4020 0%, #4a2a14 60%, #2e1a0c 100%);
  }

  /* Back-of-spread sign-off */
  .closing-mark {
    position: absolute; left: 697px; top: 742px; width: 400px;
    display: flex; align-items: center; justify-content: center; gap: 14px;
  }
  .closing-mark .brand-name { font-size: 34px; }
</style>
</head>
<body>
  <section class="back-cover">
    <div class="brand-frame">
      <span class="brand-dot"></span>
      <div class="brand-name">HARBOR TABLE<br>CATERING</div>
    </div>
    <p class="contact contact-phone">800-555-0142</p>
    <p class="contact contact-line contact-email">contact@email.com</p>
    <p class="contact contact-line contact-domain">www.domainname.com</p>
    <div class="contact-rule"></div>
    <p class="contact contact-web">www.websitehere.com</p>
  </section>

  <div class="accent-band"></div>

  <section class="front-page">
    <header class="front-header">
      <div class="brand-name">HARBOR TABLE<br>CATERING</div>
      <p class="front-intro">Fusce ac turpis quis ligula lacinia aliquet. Mauris ipsum. Nulla metus metus,<br>ullamcorper vel tincidunt sed euismod in nibh.</p>
    </header>
    <div class="photo photo-hero" role="img" aria-label="Fresh pasta nests, plain and spinach, with eggs, a mound of flour and wheat ears"></div>
    <div class="photo photo-cake" role="img" aria-label="Small bundt cakes on a woven board"></div>
    <div class="photo photo-juice" role="img" aria-label="Jugs and glasses of fruit juice with citrus fruit"></div>
    <div class="photo photo-fruit" role="img" aria-label="Whole and halved horned melons"></div>
  </section>

  <div class="closing-mark">
    <span class="brand-dot"></span>
    <div class="brand-name">HARBOR TABLE<br>CATERING</div>
  </div>
</body>
</html>
```